Website for IT consulting Company

I need a website upgrade, the existing site content is ok, I would also like to add a testimonial page, the site should be something that is easy for us to update content. You use the content from www.kelvanbrook.com as an example. I will also post update logo and artwork. I also need a contact form with some type of validation or captcha.

I added Coded to the Project

Please omit Address maps

Target Market(s)

small business, service oriented companies. We provide IT Consulting, support and mangement

Industry/Entity Type

Information Technology

Coding

Number of Pages Required

1 page

Font styles to use
Serif
Sans Serif

Requirements
Must have
• Contain logo attached, and content from existing web site www.kelvanbrook.com.
• Also need to update content easily, and be movable to different platforms.
• There is a catch phrase
• "Let us worry about your technology…” “ so you don’t have to!”
• Should be included.
Nice to have
• Testimonial page, Project page where we can post new and past projects and pictures
Should not have
• none

```html
<!DOCTYPE html>
<html lang="en">
<head>
<meta charset="utf-8">
<title>Kelvanbrook Development Group</title>
<link href="https://fonts.googleapis.com/css2?family=Montserrat:wght@400;500;600;700&family=Open+Sans:wght@400;600&display=swap" rel="stylesheet">
<style>
:root{
  --blue:#1b8fd6;
  --blue-dark:#0f6fb3;
  --blue-deep:#0a2a55;
  --navy:#061830;
  --orange:#f07a1e;
  --ink:#333;
  --muted:#8a8a8a;
  --light:#f2f2f2;
  --form-bg:#ececec;
  --white:#fff;
}
*{box-sizing:border-box;margin:0;padding:0}
html,body{width:1200px;height:3098px;overflow:hidden}
body{position:relative;font-family:"Open Sans",Arial,sans-serif;color:var(--ink);background:var(--white)}
.abs{position:absolute}
h1,h2,h3,.btn,.menu,.label{font-family:"Montserrat",Arial,sans-serif}

/* hero */
.hero{left:0;top:0;width:1200px;height:622px;background:radial-gradient(ellipse at 70% 55%,#2d6fb8 0%,#123a75 35%,var(--navy) 80%)}
.brand{left:134px;top:30px;display:flex;align-items:center;gap:14px;color:var(--white);font-family:"Montserrat",sans-serif;font-weight:700;font-size:40px;letter-spacing:1px}
.brand-mark{width:36px;height:36px;background:var(--orange)}
.menu-toggle{left:964px;top:40px;display:flex;align-items:center;gap:10px;color:var(--white);font-size:17px}
.burger{width:40px;height:20px;border-top:3px solid #fff;border-bottom:3px solid #fff;position:relative}
.burger:after{content:"";position:absolute;left:0;right:0;top:5.5px;border-top:3px solid #fff}
.dropdown{left:849px;top:91px;width:217px;background:var(--blue);list-style:none;z-index:3}
.dropdown li{height:38px;line-height:38px;padding-left:26px;color:var(--white);font-size:13px;border-bottom:1px solid rgba(255,255,255,.25);position:relative}
.dropdown li:last-child{border-bottom:0}
.dropdown .has-sub:after{content:"›";position:absolute;right:16px;font-size:22px;top:-1px}
.hero-title{left:0;top:252px;width:1200px;text-align:center;color:var(--white);font-size:38px;font-weight:600;line-height:40px;letter-spacing:1px}
.hero-btn{left:508px;top:353px;width:188px;height:46px;border:2px solid #fff;color:#fff;font-size:15px;font-weight:600;display:flex;align-items:center;justify-content:center}
.dots{left:552px;top:580px;display:flex;gap:10px}
.dots span{width:14px;height:14px;border-radius:50%;background:#fff}
.dots span.active{background:transparent;border:2px solid #fff}

/* about */
.about-art{left:0;top:622px;width:516px;height:421px;background:linear-gradient(135deg,#e9e9e9 0%,#b9b9b9 45%,#f07a1e 100%)}
.about-title{left:539px;top:700px;font-size:25px;font-weight:500;color:#333;white-space:nowrap;line-height:34px}
.about-text{left:539px;top:752px;width:540px;font-size:14px;line-height:26px;color:var(--muted)}
.btn{background:var(--blue-dark);color:#fff;font-size:13px;font-weight:600;display:flex;align-items:center;justify-content:center}
.about-btn{left:547px;top:931px;width:135px;height:38px}

/* support */
.support{left:0;top:1043px;width:1200px;height:475px;background:radial-gradient(ellipse at 50% 40%,#2aa2e6 0%,var(--blue-dark) 75%)}
.notch{left:560px;top:1043px;width:0;height:0;border-left:40px solid transparent;border-right:40px solid transparent;border-top:28px solid #fff}
.section-title{width:1200px;left:0;text-align:center;font-size:27px;font-weight:500}
.support-title{top:1084px;color:#fff}
.card{top:1134px;width:302px;height:345px;background:#fff}
.card-photo{height:167px;background:linear-gradient(135deg,#0e3f73,#4d8fc4)}
.card h3{margin-top:20px;text-align:center;font-size:19px;font-weight:500;color:var(--blue-dark)}
.card p{margin:10px 26px 0;text-align:center;font-size:12px;line-height:19px;color:var(--muted);height:57px;overflow:hidden}
.card .more{display:block;margin:14px auto 0;width:110px;text-align:center;font-family:"Montserrat",sans-serif;font-size:13px;color:var(--blue-dark);border-bottom:2px solid var(--blue-dark);padding-bottom:6px}

/* services */
.services{left:0;top:1518px;width:1200px;height:543px;background:var(--light);border-bottom:2px solid #ddd}
.services-title{top:1566px;color:#333;font-size:23px;font-weight:600}
.services svg{position:absolute;left:0;top:0}
.label{font-size:12.5px;fill:#333;font-weight:500}

/* testimonials */
.testimonials-title{top:2134px;color:var(--blue);font-size:25px}
.quote{left:300px;top:2188px;width:600px;text-align:center;font-size:16.5px;line-height:31px;color:var(--muted)}
.qmark{color:var(--blue-dark);font-family:Georgia,serif;font-size:34px;font-weight:700;line-height:0;vertical-align:-6px}
.author{left:0;top:2303px;width:1200px;text-align:center;font-size:15px;color:#555}

/* contact */
.contact{left:0;top:2375px;width:1200px;height:341px;background:var(--form-bg)}
.contact-title{top:2430px;color:var(--blue-dark);font-size:23px;font-weight:700}
.field{background:#fff;border:1px solid #d6d6d6;font-size:13px;color:#777;padding:12px 18px}
.row{left:153px;top:2486px;width:908px;display:flex;gap:8px}
.row .field{flex:1;height:42px}
.message{left:153px;top:2536px;width:908px;height:78px}
.submit{left:537px;top:2629px;width:136px;height:35px}

/* footer */
.footer{left:0;top:2716px;width:1200px;height:382px;background:linear-gradient(#d9d9d9,#a5a5a5)}
.col{top:2778px;color:#fff;font-size:13px;line-height:27px}
.col h4{font-family:"Montserrat",sans-serif;font-weight:500;font-size:16px;margin-bottom:4px}
.social{left:843px;top:2813px;display:flex;gap:7px}
.social span{width:36px;height:36px;border-radius:50%;border:2px solid #fff;background:var(--blue)}
.social span:nth-child(2){background:#2f5aa6}
.social span:nth-child(3){background:#1872b0}
.social span:nth-child(4){background:#d94b36}
.rule{left:131px;top:3015px;width:938px;border-top:1px solid rgba(255,255,255,.5)}
.copy{left:0;top:3042px;width:1200px;text-align:center;color:#fff;font-size:11px}
</style>
</head>
<body>

<header>
  <div class="abs hero" role="img" aria-label="Photo of a hand touching a glowing digital touchscreen"></div>
  <div class="abs brand"><span class="brand-mark"></span>KELVANBROOK</div>
  <div class="abs menu-toggle menu"><span class="burger"></span>MENU</div>
  <ul class="abs dropdown menu">
    <li>HOME</li><li>ABOUT US</li><li>SUPPORT</li><li class="has-sub">SERVICES</li><li>PROJECTS</li><li>CONTACT</li>
  </ul>
  <h1 class="abs hero-title">FLEXIBLE SOLUTIONS FOR YOUR<br>BUSINESS NEEDS</h1>
  <div class="abs hero-btn">QUICK CONTACT</div>
  <div class="abs dots"><span class="active"></span><span></span><span></span><span></span></div>
</header>

<section>
  <div class="abs about-art" role="img" aria-label="Illustration of a metallic cube with orange blocks breaking away"></div>
  <h2 class="abs about-title">About Kelvanbrook Development Group, Inc</h2>
  <p class="abs about-text">Kelvanbrook is a technology solution provider based in Brayford, Texas. Our goal is to make technology a non-issue for individuals and small to medium size businesses ranging from 5 to 150 Users. KDG has the experience, the tools, high-level technology solutions and training to power your business and your work force. We understand that all business's have one goal in common! (KDG) A Return on Investment</p>
  <div class="abs btn about-btn">READ MORE</div>
</section>

<section>
  <div class="abs support"></div>
  <div class="abs notch"></div>
  <h2 class="abs section-title support-title">IT SUPPORT SOLUTIONS</h2>
  <article class="abs card" style="left:130px">
    <div class="card-photo" role="img" aria-label="Photo of hands holding a tablet with digital overlays"></div>
    <h3>Managed IT Solutions</h3>
    <p>Our staff will design, service, administer and maintain your IT needs. We are well versed on all major operating system, and network platforms.</p>
    <span class="more">LEARN MORE</span>
  </article>
  <article class="abs card" style="left:448px">
    <div class="card-photo" role="img" aria-label="Photo of a technician working in a server room"></div>
    <h3>Remote Diagnostic</h3>
    <p>Do you need a quick solution to a technical problem? With our live remote-assistance tool, a member of our support team can help right away.</p>
    <span class="more">LEARN MORE</span>
  </article>
  <article class="abs card" style="left:766px">
    <div class="card-photo" role="img" aria-label="Photo of an engineer inspecting data center racks"></div>
    <h3>IT Infrastructure Design</h3>
    <p>Do you have more than one site? Do you need remote access? We can design and implement LANS/WANS and VPN's.</p>
    <span class="more">LEARN MORE</span>
  </article>
</section>

<section>
  <div class="abs services">
    <svg width="1200" height="543" viewBox="0 0 1200 543">
      <g fill="none" stroke="#3aa0dc" stroke-width="2">
        <path d="M374 543 A227 227 0 0 1 826 543"/>
      </g>
      <g stroke="#3aa0dc" stroke-width="1.5" stroke-dasharray="3 4" fill="none">
        <line x1="374" y1="497" x2="264" y2="485"/>
        <line x1="391" y1="434" x2="291" y2="392"/>
        <line x1="428" y1="374" x2="341" y2="299"/>
        <line x1="492" y1="322" x2="438" y2="221"/>
        <line x1="568" y1="297" x2="553" y2="186"/>
        <line x1="651" y1="301" x2="679" y2="180"/>
        <line x1="722" y1="331" x2="791" y2="223"/>
        <line x1="781" y1="385" x2="884" y2="306"/>
        <line x1="812" y1="440" x2="931" y2="394"/>
        <line x1="826" y1="498" x2="954" y2="485"/>
      </g>
      <g fill="#fff" stroke="#3aa0dc" stroke-width="2">
        <circle cx="374" cy="497" r="7"/><circle cx="391" cy="434" r="7"/><circle cx="428" cy="374" r="7"/>
        <circle cx="492" cy="322" r="7"/><circle cx="568" cy="297" r="7"/><circle cx="651" cy="301" r="7"/>
        <circle cx="722" cy="331" r="7"/><circle cx="781" cy="385" r="7"/><circle cx="812" cy="440" r="7"/>
        <circle cx="826" cy="498" r="7"/>
      </g>
      <g fill="#1b8fd6" stroke="#fff" stroke-width="3">
        <circle cx="264" cy="485" r="44"/><circle cx="291" cy="392" r="44"/><circle cx="341" cy="299" r="44"/>
        <circle cx="438" cy="221" r="44"/><circle cx="553" cy="186" r="44"/><circle cx="679" cy="180" r="44"/>
        <circle cx="791" cy="223" r="44"/><circle cx="884" cy="306" r="44"/><circle cx="931" cy="394" r="44"/>
        <circle cx="954" cy="485" r="44"/>
      </g>
      <g fill="none" stroke="#fff" stroke-width="3" stroke-linecap="round" stroke-linejoin="round">
        <circle cx="264" cy="485" r="13"/><circle cx="264" cy="485" r="5" fill="#fff"/>
        <path d="M264 466v6M264 498v6M245 485h6M277 485h6M251 472l4 4M273 494l4 4M277 472l-4 4M255 494l-4 4"/>
        <circle cx="291" cy="392" r="17"/><path d="M274 392h34M291 375c-8 10-8 24 0 34M291 375c8 10 8 24 0 34"/>
        <path d="M341 292v28M333 320l8-28 8 28M330 287a14 14 0 0 0 0 18M352 287a14 14 0 0 1 0 18M324 281a22 22 0 0 0 0 30M358 281a22 22 0 0 1 0 30"/>
        <rect x="421" y="210" width="24" height="22" rx="3" fill="#fff"/><path d="M445 216l12-7v24l-12-7z" fill="#fff"/>
        <path d="M553 166v40M538 176l15 10 15-10M541 196l12-8 12 8"/>
        <rect x="662" y="166" width="34" height="23" rx="2"/><path d="M679 189v7M670 197h18"/>
        <circle cx="791" cy="210" r="5"/><circle cx="777" cy="234" r="5"/><circle cx="805" cy="234" r="5"/><circle cx="791" cy="225" r="3" fill="#fff"/>
        <path d="M791 215v10M789 227l-9 4M793 227l9 4"/>
        <path d="M866 302a26 26 0 0 1 36 0M872 309a16 16 0 0 1 24 0M878 316a7 7 0 0 1 12 0"/><circle cx="884" cy="322" r="2" fill="#fff"/>
        <path d="M931 374l16 6v12c0 11-8 18-16 21-8-3-16-10-16-21v-12z"/><path d="M931 378v33"/>
        <path d="M940 494h-24a9 9 0 0 1 1-18 13 13 0 0 1 25-3 9 9 0 0 1 -2 21z" transform="translate(14 0)"/><path d="M938 502h32"/>
      </g>
      <g>
        <rect x="458" y="424" width="22" height="22" fill="#f07a1e"/>
        <text x="490" y="445" font-family="Montserrat, sans-serif" font-weight="700" font-size="27" fill="#8c8c8c">KELVANBROOK</text>
      </g>
      <g class="label" text-anchor="end">
        <text x="211" y="480">DESKTOP</text><text x="211" y="496">SUPPORT</text>
        <text x="238" y="388">NETWORK</text><text x="238" y="404">ADMINISTRATION</text>
        <text x="291" y="304">TELECOMMUNICATION</text>
        <text x="384" y="198">AUDIO/VIDEO</text><text x="384" y="214">MULTIMEDIA</text>
      </g>
      <g class="label" text-anchor="middle">
        <text x="471" y="134">DISASTER</text><text x="471" y="150">RECOVERY</text>
      </g>
      <g class="label">
        <text x="723" y="152">WEBDESIGN</text>
        <text x="840" y="202">NETWORK</text><text x="840" y="218">CABLING</text>
        <text x="940" y="296">WIRELESS</text><text x="940" y="312">NETWORKS</text>
        <text x="987" y="390">ANTIVIRUS</text><text x="987" y="406">SOLUTION</text>
        <text x="1008" y="482">CLOUD HOSTING</text><text x="1008" y="498">\VIRTUALIZATION</text>
      </g>
    </svg>
  </div>
  <h2 class="abs section-title services-title">OUR SERVICE</h2>
</section>

<section>
  <h2 class="abs section-title testimonials-title">TESTIMONIALS</h2>
  <svg class="abs" style="left:140px;top:2216px" width="26" height="54" viewBox="0 0 26 54"><path d="M22 2L4 27l18 25" fill="none" stroke="#777" stroke-width="2"/></svg>
  <svg class="abs" style="left:1018px;top:2216px" width="26" height="54" viewBox="0 0 26 54"><path d="M4 2l18 25L4 52" fill="none" stroke="#777" stroke-width="2"/></svg>
  <p class="abs quote"><span class="qmark">“</span> Morbi diam mauris viverra in gravida eu mattis in ante Morbi eget arcu Morbi porta libero id ullamcorper nonummy nibh ligula pulvinar metus eget consectetuer augue <span class="qmark">”</span></p>
  <p class="abs author">-By Author Name</p>
</section>

<section>
  <div class="abs contact"></div>
  <h2 class="abs section-title contact-title">QUICK CONTACT FORM</h2>
  <div class="abs row">
    <div class="field">First Name</div><div class="field">Last Name</div><div class="field">Email address</div><div class="field">Phone</div>
  </div>
  <div class="abs field message">Message</div>
  <div class="abs btn submit">SUBMIT</div>
</section>

<footer>
  <div class="abs footer"></div>
  <div class="abs col" style="left:151px"><h4>COMPANY</h4>Home<br>About Us<br>Our Services<br>Why Us<br>Contact</div>
  <div class="abs col" style="left:355px"><h4>RESOURCES</h4>Support<br>Solutions<br>Clients<br>Testimonials</div>
  <div class="abs col" style="left:560px"><h4>CONTACT INFO</h4>418 Meridian Park Way Suite 210<br>Ashcombe, PA 19120<br>(555) 318-4070<br>info@kelvanbrook.com</div>
  <div class="abs col" style="left:845px"><h4>FOLLOW US</h4></div>
  <div class="abs social"><span></span><span></span><span></span><span></span></div>
  <div class="abs rule"></div>
  <p class="abs copy">© 2017 Company Name. All right reserved. Term of Use</p>
</footer>

</body>
</html>
```